Vision, Mission and Culture Posters

We have written text paragraphs for our company vision and mission and need them made into a2 or a3 sized posters using our logo for inspiration for colour. Our company culture has 10 paragraphs and we'd like this to be a single poster of a2 or a1. Each poster should have the logo on and share common design. It's not a complex job really.

Industry/Entity Type

It Company

Requirements
Nice to have
• These will be going up on our office wall so need to be clear to read from a distance and look professional but also not stodgy.

```html
<!DOCTYPE html>
<html lang="en">
<head>
<meta charset="utf-8">
<title>Bayline Hire – Company Values</title>
<link href="https://fonts.googleapis.com/css2?family=Anton&family=Oswald:wght@500&family=Roboto+Condensed:wght@400;700&display=swap" rel="stylesheet">
<style>
  :root {
    --ink: #111111;
    --red: #d7262b;
    --yellow: #f3ea00;
    --panel-light: #f8f9d2;
    --panel-edge: #dbe77a;
    --paper: #ffffff;
  }
  html, body { margin: 0; padding: 0; overflow: hidden; background: var(--paper); }
  .poster {
    position: relative; width: 847px; height: 1200px; overflow: hidden;
    background: var(--paper); font-family: "Roboto Condensed", Arial, sans-serif; color: var(--ink);
  }
  .frame {
    position: absolute; left: 16px; top: 97px; width: 817px; height: 1001px;
    background: radial-gradient(ellipse at 50% 45%, var(--panel-light) 0%, #eef3a8 55%, var(--panel-edge) 100%);
    border: 2px solid var(--ink); box-sizing: border-box;
  }
  .frame::before {
    content: ""; position: absolute; inset: 6px; border: 1.5px solid var(--ink);
  }
  .corner { position: absolute; width: 10px; height: 10px; border: 2px solid var(--ink); background: var(--panel-edge); }
  .corner.tl { left: 10px; top: 89px; } .corner.tr { right: 10px; top: 89px; }
  .corner.bl { left: 10px; top: 1086px; } .corner.br { right: 10px; top: 1086px; }
  .masthead {
    position: absolute; left: 153px; top: 47px; width: 543px; height: 85px;
    background: var(--ink); border-radius: 14px; box-sizing: border-box;
    border: 3px solid var(--ink); outline: 2px solid var(--paper); outline-offset: -6px;
    display: flex; align-items: center; justify-content: center;
  }
  .masthead h1 {
    margin: 0; font-family: "Anton", Impact, sans-serif; font-weight: 400;
    color: var(--yellow); font-size: 40px; letter-spacing: 1px;
  }
  .title {
    position: absolute; left: 0; width: 847px; top: 142px; margin: 0; text-align: center;
    font-family: "Anton", Impact, sans-serif; font-weight: 400; font-size: 104px; line-height: 1;
    color: var(--paper); -webkit-text-stroke: 4px var(--ink); paint-order: stroke fill; letter-spacing: 1px;
  }
  .value { position: absolute; width: 382px; }
  .value.left { left: 30px; } .value.right { left: 430px; }
  .value h2 {
    margin: 0 0 3px; font-family: "Oswald", "Arial Narrow", sans-serif; font-weight: 500;
    font-size: 28px; line-height: 34px; display: flex; align-items: center; gap: 6px;
    text-transform: uppercase; letter-spacing: -0.3px;
  }
  .value h2.red { color: var(--red); }
  .value h2 svg { flex: none; }
  .value p { margin: 0; font-size: 11.2px; line-height: 15.3px; }
  .brand {
    position: absolute; left: 153px; top: 1021px; width: 543px; height: 160px;
    background: var(--yellow); border: 3px solid var(--ink); border-radius: 14px; box-sizing: border-box;
    display: flex; align-items: center; justify-content: center; gap: 22px;
  }
  .brand-mark { width: 54px; height: 54px; background: var(--red); }
  .brand-name { font-family: "Roboto Condensed", Arial, sans-serif; font-weight: 700; font-size: 52px; color: var(--ink); }
</style>
</head>
<body>
<div class="poster">
  <div class="frame"></div>
  <span class="corner tl"></span><span class="corner tr"></span>
  <span class="corner bl"></span><span class="corner br"></span>

  <header class="masthead"><h1>BAYLINE HIRE</h1></header>
  <h2 class="title">COMPANY VALUES</h2>

  <section class="value left" style="top:268px">
    <h2 class="red"><svg width="14" height="30" viewBox="0 0 14 30"><rect x="2" y="1" width="10" height="28" rx="5" fill="#111"/><rect x="7" y="1" width="5" height="28" rx="2" fill="#fff"/></svg>Communication</h2>
    <p>We believe in open communication providing our customers, colleagues and others with honest, accurate, concise and prompt information relevant to their needs to ensure everyone always has a sound understanding of any matter being communicated. We are polite, friendly and warm and we use good communication as a means of enhancing our customer experience.</p>
  </section>

  <section class="value left" style="top:411px">
    <h2><svg width="14" height="30" viewBox="0 0 14 30"><rect x="2" y="1" width="10" height="28" rx="5" fill="#d7262b"/><rect x="2" y="1" width="5" height="28" rx="2" fill="#111"/></svg>Education</h2>
    <p>We believe in the importance of continual learning and education and thrive on helping our colleagues by sharing our knowledge and learnings. We learn from our mistakes and use them to build a better, stronger, closer team environment. Understanding that everyone’s needs are different and that we learn in different ways, we challenge our people to constantly improve their professional development in a way that works best for them.</p>
  </section>

  <section class="value left" style="top:566px">
    <h2 class="red"><svg width="14" height="30" viewBox="0 0 14 30"><rect x="2" y="1" width="10" height="28" rx="5" fill="#111"/><rect x="7" y="1" width="5" height="28" rx="2" fill="#fff"/></svg>Professionalism</h2>
    <p>We represent ourselves as professionals and our business to the best of our abilities at all times taking particular care to give the best impression of ourselves to those we interact with during the course of our working days whether that be by phone, email or in person. We are always on time, well presented, well prepared and work hard to succeed.</p>
  </section>

  <section class="value left" style="top:709px">
    <h2><svg width="14" height="30" viewBox="0 0 14 30"><rect x="2" y="1" width="10" height="28" rx="5" fill="#d7262b"/><rect x="2" y="1" width="5" height="28" rx="2" fill="#111"/></svg>Ownership</h2>
    <p>We are each fully responsible for our roles and for our contribution to the success of our business. We are accountable for our results, our ability to improve at what we do, our mistakes and what we do to correct them.</p>
  </section>

  <section class="value left" style="top:824px">
    <h2 class="red"><svg width="14" height="30" viewBox="0 0 14 30"><rect x="2" y="1" width="10" height="28" rx="5" fill="#111"/><rect x="7" y="1" width="5" height="28" rx="2" fill="#fff"/></svg>Commercial Awareness</h2>
    <p>We understand that in a small business everything we do can impact the success of our business and we commit ourselves to thinking about the impact on our business of all the decisions we make before we make them. We consider cost against benefit, remembering the cheapest option doesn’t always give the greatest benefit, the best value use of our time, who benefits from what we do and how it benefits our business.</p>
  </section>

  <section class="value right" style="top:268px">
    <h2><svg width="14" height="30" viewBox="0 0 14 30"><rect x="2" y="1" width="10" height="28" rx="5" fill="#d7262b"/><rect x="2" y="1" width="5" height="28" rx="2" fill="#111"/></svg>Balance</h2>
    <p>We try to find the best balance in our lives between our responsibilities, obligations, duties and desires whilst still ensuring we have time to devote to friends, families, fun and life. We try to balance our opinions and thoughts with those of others and believe that with balance comes fairness, integrity, self-control and a great attitude.</p>
  </section>

  <section class="value right" style="top:411px">
    <h2 class="red"><svg width="14" height="30" viewBox="0 0 14 30"><rect x="2" y="1" width="10" height="28" rx="5" fill="#111"/><rect x="7" y="1" width="5" height="28" rx="2" fill="#fff"/></svg>Customer Service</h2>
    <p>We believe that without our customers we would not be successful and understand the outstanding level of service we give them is critical to our continued success, even down to the smallest action whenever that may be required from us. We go out of our way to help any customer with an issue and are only satisfied when we have helped them achieve a fair outcome they are happy with.</p>
  </section>

  <section class="value right" style="top:569px">
    <h2><svg width="14" height="30" viewBox="0 0 14 30"><rect x="2" y="1" width="10" height="28" rx="5" fill="#d7262b"/><rect x="2" y="1" width="5" height="28" rx="2" fill="#111"/></svg>Consistency</h2>
    <p>We believe in consistency of our work, our approach, our positive attitude and our actions to set a standard at which our colleagues and customers feel a level of familiarity that strengthens our relationship whilst representing ourselves and our business to their best.</p>
  </section>

  <section class="value right" style="top:697px">
    <h2 class="red"><svg width="14" height="30" viewBox="0 0 14 30"><rect x="2" y="1" width="10" height="28" rx="5" fill="#111"/><rect x="7" y="1" width="5" height="28" rx="2" fill="#fff"/></svg>Success</h2>
    <p>We understand success isn’t given, it is earned every day, piece by piece. We are driven to succeed as an individual and as a team and we support each other in earning that success. We are not afraid to celebrate our successes to acknowledge our hard work and dedication to our achieving our goals.</p>
  </section>

  <section class="value right" style="top:826px">
    <h2><svg width="14" height="30" viewBox="0 0 14 30"><rect x="2" y="1" width="10" height="28" rx="5" fill="#d7262b"/><rect x="2" y="1" width="5" height="28" rx="2" fill="#111"/></svg>Commitment</h2>
    <p>We are committed to the company vision, to the mission and to upholding the company culture as well as showing the company the same commitment it has shown to us. We talk about our vision, mission and culture often, use them to help guide ourselves and our colleagues as we go about our work. We are not afraid to let our colleagues know when we feel they are not showing the right commitment to our vision, mission and culture but make sure we do so in a positive and helpful way to ensure they can get back on track as easily as possible.</p>
  </section>

  <footer class="brand">
    <span class="brand-mark"></span>
    <span class="brand-name">Bayline Hire</span>
  </footer>
</div>
</body>
</html>
```